Fernhollow Brochure - A new residential property investment development in Brisbane Queensland *

I need a brochure to entice and inspire customers of financial planners and alike to buy our investment property development, Fernhollow in Greenbank, Australia.

The brochure will be approximately 16 - 18 pages long and will follow a similar format (including maps etc) to the once attached in the uploaded files, however it is important that it has it's own unique style and brand identify. You will have access to all the renders, maps and autocad drawings that will need to be included in the brochure and will be linked in my dropbox link below.

The brochure should feel sophisticated and use the logo we've previously had developed on studio hive. The background and text should also match the style guidelines of our logo's although happy for you to to get creative with the background as long as it is relevant and fits with the colours. For example stock photo's of tree's, people playing, sunlight etc are great - although the context should be in Australia.

There will be a bit of back and forth once I select the winning designer to ensure the brochure is perfect. I'll also need individual files of the masterplan.

Look forward to seeing your designs.

https://www.filecrate-example.net/sh/q8wz3mfa1tp9rdx/KPLx7vnM2_TTqeZb4Hw9kY1uc?dl=0

Target Market(s)

Financial Planners and their consumer customers

Industry/Entity Type

Real Estate Development

Font styles to use
Other font styles liked:
• Monserrat - as per branding guidelines

Requirements
Must have
• At least all the elements that exist in the example brochures and outlined in the content

dropbox link - https://www.filecrate-example.net/sh/q8wz3mfa1tp9rdx/KPLx7vnM2_TTqeZb4Hw9kY1uc?dl=0

```html
<!DOCTYPE html>
<html lang="en">
<head>
<meta charset="utf-8">
<title>Fernhollow Brochure – Contents Spread</title>
<link href="https://fonts.googleapis.com/css2?family=Montserrat:wght@300;400;500&display=swap" rel="stylesheet">
<style>
  :root {
    --backdrop: #a3a3a3;
    --paper: #ffffff;
    --paper-shade: #ececec;
    --brand-blue: #3f6f91;
    --brand-blue-light: #6f98b3;
    --brand-blue-deep: #2f5b7c;
    --photo-dark: #1f2a36;
    --photo-mid: #4a5a6b;
    --photo-green: #6f8a5a;
    --photo-light: #b9c4a8;
    --text-light: #e9eef2;
  }
  * { margin: 0; padding: 0; box-sizing: border-box; }
  html, body {
    width: 1200px; height: 900px; overflow: hidden;
    background: var(--backdrop);
    font-family: "Montserrat", sans-serif;
  }
  .spread {
    position: absolute; left: 100px; top: 200px;
    width: 1000px; height: 500px;
    display: flex;
    box-shadow: 0 18px 40px rgba(0,0,0,0.25);
  }
  .page {
    position: relative; width: 500px; height: 500px;
    background: var(--paper); overflow: hidden;
  }
  .page--left { background: linear-gradient(90deg, var(--paper) 85%, var(--paper-shade)); }
  .page--right { background: linear-gradient(90deg, var(--paper-shade), var(--paper) 12%); }

  .lifestyle-photo {
    position: absolute; top: 70px; height: 370px;
  }
  .page--left .lifestyle-photo {
    left: 0; width: 500px;
    background: linear-gradient(100deg, var(--photo-dark) 0%, var(--photo-mid) 35%, #5e6e58 65%, var(--photo-green) 100%);
  }
  .page--right .lifestyle-photo {
    left: 0; width: 150px;
    background: linear-gradient(100deg, var(--photo-green) 0%, var(--photo-light) 100%);
  }

  .tagline {
    position: absolute; left: 46px; top: 250px;
    color: var(--text-light);
    font-weight: 300; font-size: 17px; line-height: 1.2;
    letter-spacing: 0.5px;
  }

  .contents-panel {
    position: absolute; left: 150px; top: 0; width: 350px; height: 500px;
    background: linear-gradient(200deg, var(--brand-blue-light) 0%, var(--brand-blue) 45%, var(--brand-blue-deep) 100%);
  }
  .contents-foot {
    position: absolute; left: 0; top: 440px; width: 150px; height: 60px;
    background: var(--brand-blue-deep);
  }
  .contents-list {
    position: absolute; left: 200px; top: 300px;
    list-style: none;
    color: var(--text-light);
    font-weight: 500; font-size: 9px;
    letter-spacing: 1.6px; text-transform: uppercase;
  }
  .contents-list li { line-height: 21px; }
</style>
</head>
<body>
  <main class="spread">
    <section class="page page--left">
      <div class="lifestyle-photo" role="img" aria-label="Lifestyle photograph of a person holding a coffee cup at an outdoor café, soft green background"></div>
      <p class="tagline">Creating<br>a sense<br>of place</p>
    </section>
    <section class="page page--right">
      <div class="lifestyle-photo" role="img" aria-label="Continuation of the café lifestyle photograph"></div>
      <div class="contents-panel"></div>
      <div class="contents-foot"></div>
      <ul class="contents-list">
        <li>About</li>
        <li>Location Proximity</li>
        <li>Sense of Community</li>
        <li>Investment</li>
        <li>Points of Interest</li>
        <li>Masterplan</li>
        <li>House Plans</li>
        <li>Package Inclusions</li>
      </ul>
    </section>
  </main>
</body>
</html>
```